Vorn upkeep KT Solar Venture

Solar power system install
Services and maintenance
wiring, Rewinding and Renovation
Switch Board Upgrade
Power and lighting point
t doesn’t matter how much you spend on quality parts, your solar system will let you down if your design and installation are sub-par. Have your solar system tailored and installed by our Master Electrician and Bright Grid Guild Accredited team.

Target Market(s)

sales and installed

Industry/Entity Type

Solar install and retailer

Contact Information for Business Card

Name , Email, Phone Number ,Business address,

Font styles to use
Serif

Colors
0054AA
0677BA
7BADD7
CADEEF
E8F1F8

Requirements
Must have
• clear and bright
Nice to have
• new design
Should not have
• unclear pictures

```html
<!DOCTYPE html>
<html lang="en">
<head>
<meta charset="utf-8">
<title>Vorn upkeep · KT Solar Venture — Business Card</title>
<link href="https://fonts.googleapis.com/css2?family=Roboto:wght@400;500;700&display=swap" rel="stylesheet">
<style>
  :root {
    --stage: #2e2e2e;
    --card: #f1f1f1;
    --card-edge: #e4e4e4;
    --blue-deep: #0054AA;
    --blue: #0677BA;
    --blue-soft: #7BADD7;
    --blue-pale: #CADEEF;
    --green: #3aa53a;
    --green-band: #6aaa3a;
    --ink: #1d1d1d;
    --band-text: #eef5f0;
  }
  * { box-sizing: border-box; margin: 0; padding: 0; }
  html, body { width: 1200px; height: 1138px; overflow: hidden; }
  body {
    background: var(--stage);
    font-family: "Roboto", Arial, sans-serif;
    position: relative;
  }
  .card {
    position: absolute;
    background: linear-gradient(180deg, #f7f7f7 0%, var(--card) 60%, var(--card-edge) 100%);
    border-radius: 18px;
    overflow: hidden;
  }

  /* ---------- front ---------- */
  .card--front { left: 274px; top: 186px; width: 623px; height: 376px; }
  .brand {
    position: absolute;
    display: flex;
    align-items: center;
    gap: 18px;
  }
  .brand__dot {
    width: 86px; height: 86px;
    border-radius: 50%;
    background: var(--blue);
    flex: none;
  }
  .brand__name {
    font-weight: 700;
    color: var(--blue-deep);
    text-transform: uppercase;
    line-height: 1.12;
    letter-spacing: 1px;
  }
  .card--front .brand { left: 110px; top: 62px; }
  .card--front .brand__name { font-size: 32px; }

  .services-band {
    position: absolute;
    left: 0; top: 238px;
    width: 100%; height: 75px;
    background: linear-gradient(90deg, var(--green-band) 0%, #4f9d63 35%, var(--blue) 70%, var(--blue) 100%);
    color: var(--band-text);
    font-size: 16.5px;
    text-align: center;
    display: flex;
    flex-direction: column;
    justify-content: center;
    gap: 5px;
  }
  .web-line {
    position: absolute;
    left: 0; top: 332px;
    width: 100%;
    display: flex;
    justify-content: center;
    align-items: center;
    gap: 24px;
    font-size: 16px;
    color: var(--ink);
  }
  .web-line__rule { width: 80px; height: 2px; }
  .web-line__rule--blue { background: linear-gradient(90deg, transparent, var(--blue)); }
  .web-line__rule--green { background: linear-gradient(90deg, var(--green), transparent); }

  /* ---------- back ---------- */
  .card--back { left: 276px; top: 608px; width: 618px; height: 374px; }
  .card--back .brand {
    left: 50px; top: 42px;
    flex-direction: column;
    align-items: center;
    gap: 14px;
  }
  .card--back .brand__dot { width: 110px; height: 110px; }
  .card--back .brand__name { font-size: 28px; text-align: center; }

  .person {
    position: absolute;
    right: 28px; top: 40px;
    text-align: right;
    color: var(--ink);
  }
  .person__name { font-size: 26px; font-weight: 700; color: var(--blue-deep); }
  .person__role { font-size: 16px; margin-top: 6px; }
  .person__address { font-size: 16px; margin-top: 26px; line-height: 24px; }

  .wave { position: absolute; left: 0; top: 0; width: 100%; height: 100%; }
  .turbines {
    position: absolute;
    left: 95px; top: 280px;
    width: 48px; height: 28px;
    background: linear-gradient(180deg, rgba(106,170,58,0.15), rgba(106,170,58,0.55));
    border-radius: 4px;
  }
  .contacts {
    position: absolute;
    right: 28px; top: 270px;
    list-style: none;
    color: #fff;
    font-size: 16px;
  }
  .contacts li {
    display: flex;
    justify-content: flex-end;
    align-items: center;
    gap: 14px;
    height: 24px;
  }
  .contacts svg { width: 14px; height: 14px; flex: none; }
</style>
</head>
<body>

<section class="card card--front">
  <div class="brand">
    <span class="brand__dot"></span>
    <div class="brand__name">Vorn upkeep<br>KT Solar Venture</div>
  </div>
  <div class="services-band">
    <p>Solar Power System Install &nbsp;|&nbsp; Wiring, Rewinding &amp; Renovation</p>
    <p>Services &amp; Maintenance &nbsp;|&nbsp; Switch Board Upgrade &nbsp;|&nbsp; Power &amp; Lighting Point</p>
  </div>
  <div class="web-line">
    <span class="web-line__rule web-line__rule--blue"></span>
    <span>www.ktsolarventure.com</span>
    <span class="web-line__rule web-line__rule--green"></span>
  </div>
</section>

<section class="card card--back">
  <svg class="wave" viewBox="0 0 618 374" preserveAspectRatio="none" aria-hidden="true">
    <path fill="var(--green)" d="M0,296 C100,318 220,330 310,290 C380,252 440,218 510,206 C560,198 600,197 618,198 L618,211 C595,210 560,212 520,220 C455,234 395,264 325,304 C235,346 110,334 0,314 Z"/>
    <path fill="var(--blue)" d="M0,330 C120,352 240,352 320,310 C380,270 420,245 470,236 C540,224 590,226 618,228 L618,374 L0,374 Z"/>
  </svg>
  <div class="turbines" role="img" aria-label="Small wind turbines on a green hill"></div>

  <div class="brand">
    <span class="brand__dot"></span>
    <div class="brand__name">Vorn upkeep<br>KT Solar Venture</div>
  </div>

  <div class="person">
    <h1 class="person__name">Elian Marsh</h1>
    <p class="person__role">Managing Director</p>
    <p class="person__address">58 Ridgeway Rd., Fernvale,<br>Lakeport, US 204817</p>
  </div>

  <ul class="contacts">
    <li>555-240-7316
      <svg viewBox="0 0 16 16"><path fill="#fff" d="M3 2h3l1.5 3.5-2 1.3a8 8 0 0 0 3.7 3.7l1.3-2L14 10v3a1 1 0 0 1-1 1A12 12 0 0 1 2 3a1 1 0 0 1 1-1z"/></svg>
    </li>
    <li>elian@ktsolarventure.com
      <svg viewBox="0 0 16 16"><rect x="1" y="3" width="14" height="10" fill="none" stroke="#fff" stroke-width="1.5"/><path d="M1 3l7 6 7-6" fill="none" stroke="#fff" stroke-width="1.5"/></svg>
    </li>
    <li>www.ktsolarventure.com
      <svg viewBox="0 0 16 16"><circle cx="8" cy="8" r="6.5" fill="none" stroke="#fff" stroke-width="1.3"/><ellipse cx="8" cy="8" rx="3" ry="6.5" fill="none" stroke="#fff" stroke-width="1.1"/><path d="M1.5 8h13M2.5 5h11M2.5 11h11" stroke="#fff" stroke-width="1"/></svg>
    </li>
  </ul>
</section>

</body>
</html>
```